Food broker, trader, wholesaler, liquidator looking for a 5 pages website

Looking for a 5 pages website design. We are food brokers, traders, wholesaler and closeout buyer working with manufacturers, distributors, importers sell to retailers, food service operators and industrial (ingredients). We help market their products. We are a resource for those who need a solution in the distribution/selling/placement of food on the shelves, kitchens and pantries. Whether we open new accounts with new products or sell short dated inventory, we know where to go and get results.

Target Market(s)

Food manufacturers, food distributors, food brokers

Coding

Coded - Design and coding required

Number of Pages Required

4 page

Font styles to use
Serif

Requirements
Must have
• Food-food production-warehouse-Food packaging-people meeting-trucks-supermarket shelves-

```html
<!DOCTYPE html>
<html lang="en">
<head>
<meta charset="utf-8">
<title>Saltmarsh Provisions</title>
<link href="https://fonts.googleapis.com/css2?family=Poppins:wght@400;500;600;700&family=Libre+Baskerville:wght@700&family=Open+Sans:wght@400&display=swap" rel="stylesheet">
<style>
:root{
  --navy:#15176a;
  --navy-dark:#0f1155;
  --ink:#2b2b2b;
  --muted:#555;
  --grey-bg:#ececec;
  --footer:#1d1d1d;
  --tab:#2f3b45;
  --tab-light:#6f767c;
  --white:#fff;
}
*{margin:0;padding:0;box-sizing:border-box}
html,body{width:1200px;height:3668px;overflow:hidden;background:var(--white)}
body{font-family:"Poppins",sans-serif;color:var(--ink);position:relative}
.abs{position:absolute}
/* header */
.top-tab{top:0;height:43px;color:var(--white);font-size:15px;display:flex;align-items:center;justify-content:center;gap:8px}
.tab-phone{left:541px;width:230px;background:var(--tab);clip-path:polygon(0 0,100% 0,92% 100%,8% 100%)}
.tab-mail{left:759px;width:326px;background:var(--tab-light);clip-path:polygon(0 0,100% 0,94% 100%,6% 100%)}
.brand{left:112px;top:20px;display:flex;align-items:center;gap:12px}
.brand-dot{width:52px;height:52px;border-radius:50%;background:var(--navy)}
.brand-name{font-family:"Poppins",sans-serif;font-weight:700;font-size:19px;color:var(--navy);letter-spacing:.5px}
.nav{top:94px;left:515px;display:flex;gap:0;font-size:16px}
.nav a{color:#222;text-decoration:none;padding:6px 11px;margin-right:12px}
.nav a.active{background:#e4e4ea;border-radius:20px}
/* hero */
.hero{top:147px;left:0;width:1200px;height:634px;background:
  linear-gradient(rgba(0,0,0,.35),rgba(0,0,0,.35)),
  radial-gradient(ellipse at 50% 45%,#c9c2a0 0%,#7b8a55 35%,#3d5233 70%,#2a2c26 100%)}
.hero-title{top:310px;width:1200px;text-align:center;font-family:"Libre Baskerville",serif;font-size:52px;color:var(--white);letter-spacing:1px}
.hero-sub{top:395px;left:260px;width:680px;text-align:center;color:var(--white);font-size:19px;font-weight:500;line-height:29px}
.btn-ghost{left:530px;top:487px;width:140px;height:55px;border:2px solid var(--white);border-radius:28px;color:var(--white);font-size:19px;display:flex;align-items:center;justify-content:center}
.dots{top:629px;left:564px;display:flex;gap:5px}
.dots span{width:20px;height:20px;border-radius:50%;background:rgba(255,255,255,.45)}
.dots span:first-child{background:var(--white)}
/* headings */
.sec-title{width:1200px;text-align:center;color:var(--navy);font-weight:700;font-size:33px}
.sec-sub{text-align:center;font-size:14px;line-height:26px;color:#333}
/* process */
.node-label{font-size:20px;font-weight:500;color:#333;line-height:28px}
.click{font-family:"Open Sans",sans-serif;font-size:15px;color:#444;text-decoration:underline}
/* about */
.about{top:1509px;left:0;width:1200px;height:658px;background:linear-gradient(90deg,#e4e4e4,#f4f4f4 55%,#e2e2e2)}
.about-title{top:1668px;left:111px;color:var(--navy);font-weight:700;font-size:32px}
.about-text{left:111px;width:545px;font-size:13.5px;line-height:25.6px;color:#444}
.btn-solid{background:var(--navy);color:var(--white);border-radius:26px;display:flex;align-items:center;justify-content:center;font-size:16px}
.about-photo{left:783px;top:1587px;width:417px;height:580px;background:radial-gradient(ellipse at 55% 60%,#d23a32 0%,#c9a278 45%,#e7e7e7 75%)}
.about-tag{left:688px;top:2073px;width:415px;height:79px;background:var(--white);color:var(--navy);font-weight:700;font-size:31px;display:flex;align-items:center;justify-content:center}
/* testimonials */
.card{background:var(--white);box-shadow:0 2px 10px rgba(0,0,0,.14)}
.avatar{width:92px;height:92px;border-radius:50%;background:linear-gradient(135deg,#c8a58a,#6f5a4c)}
.t-name{font-size:14.5px;font-weight:500;color:#222}
.t-role{font-size:11px;color:#444;margin-top:2px}
.t-text{font-size:11.5px;line-height:18px;color:#555;text-align:justify;margin-top:14px}
.quote{font-size:56px;font-weight:700;color:var(--navy);line-height:1}
/* news */
.news-card{width:311px;height:419px;top:2830px;background:var(--white)}
.news-img{width:311px;height:185px;position:relative}
.news-date{position:absolute;top:148px;width:100%;text-align:center;font-size:12px;font-weight:600;color:#111;z-index:2}
.news-title{text-align:center;font-size:19px;font-weight:500;color:#111;margin-top:30px}
.news-text{text-align:center;font-size:13.5px;line-height:20px;color:#333;padding:0 22px;margin-top:10px}
.news-btn{width:113px;height:45px;margin:18px auto 0}
/* footer */
.foot-brand{top:3295px;width:1200px;display:flex;flex-direction:column;align-items:center;gap:8px}
.foot-dot{width:100px;height:72px;border-radius:50%;background:var(--white)}
.foot-name{color:var(--white);font-weight:700;font-size:14px;letter-spacing:.5px}
.foot-contact{top:3448px;left:316px;display:flex;gap:26px;color:var(--white);font-size:20px;align-items:center}
.foot-contact span{display:flex;align-items:center;gap:12px}
.ring{width:44px;height:44px;border:2px solid var(--white);border-radius:50%;display:flex;align-items:center;justify-content:center}
.foot-nav{top:3525px;width:1200px;text-align:center;color:var(--white);font-size:17px}
.foot-nav i{font-style:normal;margin:0 14px}
.foot-rule{top:3583px;left:111px;width:975px;height:1px;background:#555}
.copy{top:3611px;width:1200px;text-align:center;color:var(--white);font-size:16px}
</style>
</head>
<body>

<!-- header -->
<div class="abs top-tab tab-phone">
  <svg width="18" height="18" viewBox="0 0 24 24" fill="none" stroke="#fff" stroke-width="2"><path d="M5 3h4l2 5-3 2a12 12 0 0 0 6 6l2-3 5 2v4a2 2 0 0 1-2 2A18 18 0 0 1 3 5a2 2 0 0 1 2-2z"/></svg>
  1800 555 014
</div>
<div class="abs top-tab tab-mail">
  <svg width="18" height="14" viewBox="0 0 24 18" fill="none" stroke="#fff" stroke-width="2"><rect x="1" y="1" width="22" height="16"/><path d="M1 1l11 9 11-9"/></svg>
  info@saltmarshprovisions.com
</div>
<div class="abs brand"><div class="brand-dot"></div><div class="brand-name">SALTMARSH PROVISIONS</div></div>
<nav class="abs nav">
  <a class="active">HOME</a><a>ABOUT US</a><a>WHAT WE DO</a><a>CONTACT</a><a>GIVING BACK</a>
</nav>

<!-- hero -->
<div class="abs hero" role="img" aria-label="Supermarket aisle seen from behind a shopping trolley, shelves blurred"></div>
<svg class="abs" style="top:660px;left:0" width="1200" height="122"><path d="M0 121 C300 10 900 10 1200 121 L1200 122 L0 122 Z" fill="#fff"/></svg>
<h1 class="abs hero-title">SALTMARSH PROVISIONS</h1>
<p class="abs hero-sub">We are food brokers, traders, wholesaler and closeout buyer working with manufacturers, distributors</p>
<div class="abs btn-ghost">Read More</div>
<div class="abs dots"><span></span><span></span><span></span></div>

<!-- how it works -->
<h2 class="abs sec-title" style="top:780px">HOW IT WORKS</h2>
<p class="abs sec-sub" style="top:833px;left:260px;width:680px">Saltmarsh Provisions works with food manufacturers, brand owners, distributors and wholesalers market their products.</p>

<svg class="abs" style="top:0;left:0" width="1200" height="1450">
  <defs>
    <marker id="tri" viewBox="0 0 10 10" refX="5" refY="5" markerWidth="16" markerHeight="16" orient="auto"><path d="M0 0L10 5L0 10Z" fill="#111"/></marker>
  </defs>
  <g stroke="#15176a" stroke-width="2" stroke-dasharray="7 5" fill="none">
    <path d="M388 1036 L383 1072" marker-end="url(#tri)"/><path d="M383 1072 L376 1103"/>
    <path d="M402 1201 L420 1230" marker-end="url(#tri)"/><path d="M420 1230 L445 1250"/>
    <path d="M526 1318 Q560 1330 602 1332" marker-end="url(#tri)"/><path d="M602 1332 Q645 1330 688 1318"/>
    <path d="M770 1250 L788 1226" marker-end="url(#tri)"/><path d="M788 1226 L806 1200"/>
    <path d="M818 1103 L814 1068" marker-end="url(#tri)"/><path d="M814 1068 L808 1035"/>
  </g>
  <circle cx="599" cy="1085" r="121" fill="#fff" stroke="#15176a" stroke-width="5" style="filter:drop-shadow(0 3px 6px rgba(0,0,0,.25))"/>
  <circle cx="599" cy="1058" r="32" fill="#15176a"/>
  <text x="599" y="1125" text-anchor="middle" font-family="Poppins,sans-serif" font-weight="700" font-size="14" fill="#15176a">SALTMARSH PROVISIONS</text>
  <g fill="#fff" stroke="#444" stroke-width="4">
    <circle cx="416" cy="985" r="48"/><circle cx="383" cy="1153" r="48"/><circle cx="478" cy="1288" r="48"/>
    <circle cx="736" cy="1288" r="48"/><circle cx="821" cy="1153" r="48"/><circle cx="791" cy="985" r="48"/>
  </g>
  <g fill="none" stroke="#15176a" stroke-width="2.5">
    <!-- production: conveyor tray -->
    <path d="M396 992 h40 l-6 10 h-28 z"/><path d="M402 992 q4 -18 20 -16 q10 2 10 16"/>
    <!-- warehouse -->
    <path d="M363 1173 v-26 l20 -14 l20 14 v26 z"/><rect x="373" y="1155" width="20" height="18"/><path d="M373 1164 h20 M383 1155 v18"/>
    <!-- packaging -->
    <rect x="462" y="1276" width="18" height="28"/><path d="M466 1276 v-8 h10 v8"/><rect x="482" y="1288" width="14" height="16"/>
    <!-- people meeting -->
    <circle cx="736" cy="1292" r="7"/><circle cx="736" cy="1266" r="4"/><path d="M729 1280 h14"/><circle cx="718" cy="1302" r="4"/><circle cx="754" cy="1302" r="4"/>
    <!-- truck -->
    <rect x="800" y="1140" width="30" height="22"/><path d="M830 1148 h10 l6 8 v6 h-16"/><circle cx="808" cy="1166" r="4"/><circle cx="836" cy="1166" r="4"/>
    <!-- shelves -->
    <path d="M771 1005 v-38 M811 1005 v-38 M771 1005 h40 M771 992 h40 M771 979 h40"/><rect x="777" y="983" width="6" height="8"/><rect x="797" y="996" width="8" height="8"/>
  </g>
</svg>

<div class="abs node-label" style="top:947px;left:180px;width:164px;text-align:right">FOOD<br>PRODUCTION</div>
<div class="abs click" style="top:1007px;left:244px;width:100px;text-align:right">Click Here</div>
<div class="abs node-label" style="top:1125px;left:160px;width:156px;text-align:right">WAREHOUSE</div>
<div class="abs click" style="top:1158px;left:216px;width:100px;text-align:right">Click Here</div>
<div class="abs node-label" style="top:1365px;left:351px;width:240px;text-align:center">FOOD PACKAGING</div>
<div class="abs click" style="top:1400px;left:421px;width:100px;text-align:center">Click Here</div>
<div class="abs node-label" style="top:1365px;left:609px;width:240px;text-align:center">PEOPLE MEETING</div>
<div class="abs click" style="top:1400px;left:679px;width:100px;text-align:center">Click Here</div>
<div class="abs node-label" style="top:1125px;left:883px">TRUCKS</div>
<div class="abs click" style="top:1158px;left:883px">Click Here</div>
<div class="abs node-label" style="top:947px;left:850px">SUPERMARKET<br>SHELVES</div>
<div class="abs click" style="top:1007px;left:851px">Click Here</div>

<!-- about -->
<section class="abs about"></section>
<div class="abs" style="top:1600px;left:111px;width:52px;height:52px;border-radius:50%;background:var(--navy)"></div>
<h2 class="abs about-title">ABOUT SALTMARSH PROVISIONS</h2>
<p class="abs about-text" style="top:1727px">Founded in 2008, Saltmarsh Provisions started with the distribution of gluten free products understanding the need to provide access to unique flavors and products for the celiac consumers. From this, we expanded into deli, dairy, groceries, frozen and beverages.</p>
<p class="abs about-text" style="top:1838px">We pride ourselves in working in an easy, personal and accessible environment making our customers and vendors comfortable with us.<br>We look forward to connecting with you and evaluating how we can assist you reaching your sales objectives.</p>
<p class="abs about-text" style="top:1957px;font-size:15px">Welcome and thank you for visiting saltmarshprovisions.com</p>
<div class="abs btn-solid" style="left:112px;top:2021px;width:124px;height:50px">Read More</div>
<div class="abs about-photo" role="img" aria-label="Delivery man in a red cap and shirt holding a paper grocery bag"></div>
<div class="abs about-tag">SALTMARSH PROVISIONS</div>

<!-- testimonials -->
<h2 class="abs sec-title" style="top:2258px">OUR TESTIMONIALS</h2>
<p class="abs sec-sub" style="top:2309px;left:220px;width:760px">Nemo enim ipsam voluptatem quia voluptas sit aspernatur aut odit aut fugit, sed quia consequuntur magni dolores eos qui ratione voluptatem.</p>

<div class="abs card" style="left:124px;top:2443px;width:280px;height:193px">
  <div class="abs avatar" role="img" aria-label="Customer portrait" style="left:0;top:0"></div>
  <div class="abs quote" style="left:24px;top:118px">“</div>
  <div class="abs" style="left:104px;top:22px;width:160px"><div class="t-name">Clara Benning</div><div class="t-role">Officer</div><p class="t-text">Nemo enim ipsam volup tatem quia voluptas sit aspernatur aut odit aut fugit, sed quia consequuntur magni dolores eos qui ra tione voluptatem.</p></div>
</div>
<div class="abs card" style="left:444px;top:2430px;width:322px;height:221px">
  <div class="abs avatar" role="img" aria-label="Customer portrait" style="left:0;top:0;width:102px;height:102px"></div>
  <div class="abs quote" style="left:30px;top:130px;font-size:64px">“</div>
  <div class="abs" style="left:120px;top:20px;width:185px"><div class="t-name" style="font-size:16px">Marcus Holloway</div><div class="t-role" style="font-size:12px">Officer</div><p class="t-text" style="font-size:13px;line-height:20.5px">Nemo enim ipsam volup tatem quia voluptas sit aspernatur aut odit aut fugit, sed quia consequuntur magni dolores eos qui ra tione voluptatem.</p></div>
</div>
<div class="abs card" style="left:801px;top:2443px;width:284px;height:193px">
  <div class="abs avatar" role="img" aria-label="Customer portrait" style="left:0;top:0"></div>
  <div class="abs quote" style="left:26px;top:118px">“</div>
  <div class="abs" style="left:106px;top:22px;width:162px"><div class="t-name">Luca Ferrand</div><div class="t-role">Officer</div><p class="t-text">Nemo enim ipsam volup tatem quia voluptas sit aspernatur aut odit aut fugit, sed quia consequuntur magni dolores eos qui ra tione voluptatem.</p></div>
</div>

<!-- news -->
<h2 class="abs sec-title" style="top:2746px">LATEST NEWS</h2>
<svg class="abs" style="top:2990px;left:0" width="1200" height="678"><path d="M0 100 C250 30 950 30 1200 100 V678 H0 Z" fill="#1d1d1d"/></svg>

<article class="abs news-card" style="left:112px">
  <div class="news-img" role="img" aria-label="Shopper handing over a paper bag at a doorway" style="background:linear-gradient(135deg,#2f4a5a,#c99a3c 60%,#e6d2a8)">
    <svg class="abs" style="bottom:0;left:0" width="311" height="60"><path d="M0 60 C80 25 200 5 311 0 V60 Z" fill="#fff"/></svg>
  </div>
  <h3 class="news-title">DUIS AUTE IRURE</h3>
  <p class="news-text">Nemo enim ipsam voluptatem quia vo luptas sit aspernatur aut odit aut fugit, sed quias.</p>
  <div class="btn-solid news-btn">Read More</div>
</article>
<article class="abs news-card" style="left:446px">
  <div class="news-img" role="img" aria-label="Crate of fresh vegetables being handed over" style="background:linear-gradient(135deg,#7aa070,#c9513c 45%,#e8e6df)">
    <svg class="abs" style="bottom:0;left:0" width="311" height="60"><path d="M0 15 C100 45 211 45 311 15 V60 H0 Z" fill="#fff"/></svg>
    <div class="news-date">MAY 10, 2019</div>
  </div>
  <h3 class="news-title" style="margin-top:24px">DUIS AUTE IRURE</h3>
  <p class="news-text">Nemo enim ipsam voluptatem quia vo luptas sit aspernatur aut odit aut fugit, sed quias.</p>
  <div class="btn-solid news-btn">Read More</div>
</article>
<article class="abs news-card" style="left:777px">
  <div class="news-img" role="img" aria-label="Gloved hands stacking food boxes" style="background:linear-gradient(135deg,#b9743c,#e6e1dc 45%,#2a3a8a)">
    <svg class="abs" style="bottom:0;left:0" width="311" height="60"><path d="M0 0 C110 5 230 25 311 60 H0 Z" fill="#fff"/></svg>
  </div>
  <h3 class="news-title">DUIS AUTE IRURE</h3>
  <p class="news-text">Nemo enim ipsam voluptatem quia vo luptas sit aspernatur aut odit aut fugit, sed quias.</p>
  <div class="btn-solid news-btn">Read More</div>
</article>

<!-- footer -->
<div class="abs foot-brand"><div class="foot-dot"></div><div class="foot-name">SALTMARSH PROVISIONS</div></div>
<div class="abs foot-contact">
  <span><span class="ring"><svg width="20" height="20" viewBox="0 0 24 24" fill="none" stroke="#fff" stroke-width="2"><path d="M5 3h4l2 5-3 2a12 12 0 0 0 6 6l2-3 5 2v4a2 2 0 0 1-2 2A18 18 0 0 1 3 5a2 2 0 0 1 2-2z"/></svg></span>1800 555 014</span>
  <span><span class="ring"><svg width="18" height="14" viewBox="0 0 24 18" fill="none" stroke="#fff" stroke-width="2"><rect x="1" y="1" width="22" height="16"/><path d="M1 1l11 9 11-9"/></svg></span>sales@saltmarshprovisions.au</span>
</div>
<nav class="abs foot-nav">HOME<i>|</i>ABOUT US<i>|</i>WHAT WE DO<i>|</i>CONTACT<i>|</i>GIVING BACK<i>|</i>CONTACT US</nav>
<div class="abs foot-rule"></div>
<p class="abs copy">Copyrights @ 2020 Saltmarsh Provisions. All Rights Reserved.</p>

</body>
</html>
```